Agrarhandel benötigt Homepage
Zielgruppe
Wir sind ein Agrarhandel mit einem Warenumschlagslager im Sinne eines klassischen Einzelhandels und vertreiben Produkte an Landwirte.
Wir vertreiben folgende Hauptproduktgruppen:
Einzelfuttermittel
wie z.B. Sojaexktraktionsschrot. Die einzelnen Produkte könnten z.B. wie die Futtermittel auf folgender Seite dargestellt werden (https://www.kornprobe-beispiel.eu/de/produkt/trelomixan)
Mischfuttermittel
Hier bieten wir unseren Kunden an, individuelles Mischfutter auf Basis unserer Einzelfuttermittel herzustellen.
Weitere Details und weitere Produktbereiche habe ich in einer Powerpoint-Übersicht dargestellt.
Neben diesen Produkten wollen wir uns als Familienunternehmen selbst vorstellen. Zudem betreiben wir in unserer Familie zusätzlich einen Milchviehbetrieb den wir ebenfalls hervorheben möchten, da wir unseren Kunden gegenüber einerseits als Zulieferer aber auch als Kollege auftreten wollen.
Einzelfuttermittel: Hier können wir durch unsere Unabhängigkeit punkten, da wir nicht abhängig von bestimmten Lieferanten sind und dementsprechend unabhängig beraten können. Wir untersuchen im Vergleich zu unseren Wettbewerben die Qualität der Futtermittel bis ins Detail und können daher eine Transparenz bieten, die Konkurrenten in der Regel nicht bieten können. Unser Warenumschlagsplatz mit moderner Technik ermöglicht es uns äußerst kosteneffizient die Waren umschlagen und ausliefern zu können.
Mischfuttermittel: Auf Basis der vorhandenen Einzelfuttermittel stellen wir je nach Kundenwunsch individuelle Mischfutter her. Wir arbeiten mit offenen Deklarationen, sodass unsere Kunden jederzeit nachvollziehen können, ob auch die Einzelfuttermittel verwendet wurden, die sie bestellt haben und keine billigen Ersatzprodukte verwendet wurden.
Zudem sind wir BT und HUPA zertifiziert. Die aktuellen für unser Unternehmen ausgestellten Zertifikate müssen für unsere Kunden als Download zur Verfügung stehen. Statt dem HUPA-Logo bitte das ..
Aufgabenstellung
Wir möchten gerne ein zeitgemäße Homepage, jedoch muss auch berücksichtigt werden, dass unsere Kunden eher konservativ denken.

```html
<!DOCTYPE html>
<html lang="de">
<head>
<meta charset="utf-8">
<title>Auental Landhandel – Produkte</title>
<link rel="stylesheet" href="https://fonts.googleapis.com/css2?family=Inter:ital,wght@0,400;0,500;0,600;0,700;0,800;1,500&display=swap">
<style>
:root{
  --green:#4b6a1d;
  --orange:#f4a812;
  --yellow:#f5c91c;
  --ink:#111111;
  --grey-bar:#dcdcdc;
  --grey-line:#d6d6d6;
  --footer:#262626;
  --white:#ffffff;
  --heart:#e3262e;
  --leaf:#25a244;
}
*{box-sizing:border-box;margin:0;padding:0}
html,body{width:1200px;height:3704px;overflow:hidden}
body{position:relative;background:var(--white);font-family:"Inter",sans-serif;color:var(--ink)}
.abs{position:absolute}

/* header */
.site-header{left:0;top:0;width:1200px;height:115px;background:var(--green)}
.header-accent{left:0;top:0;width:69px;height:115px;background:var(--orange)}
.header-gap{left:69px;top:0;width:15px;height:115px;background:#cfcfcf}
.header-rule{left:0;top:115px;width:1200px;height:10px;background:var(--grey-line)}
.brand{left:112px;top:30px;width:120px;text-align:center;color:var(--orange);font-weight:700;font-size:17px;line-height:1.05}
.brand-dot{display:block;margin:0 auto 5px;width:22px;height:22px;border-radius:50%;background:var(--orange)}
.main-nav{top:55px;left:484px;display:flex;gap:16px;font-size:13px;font-weight:700;color:var(--white);letter-spacing:.1px}
.main-nav .active{color:var(--orange)}
.search-icon{left:1144px;top:49px}
.dropdown{left:829px;top:79px;width:134px;height:82px;background:var(--yellow);padding:4px 5px;font-size:8px;font-weight:700;color:#222}
.dropdown li{list-style:none;height:20.5px;line-height:20px;border-bottom:1px solid rgba(0,0,0,.1)}
.dropdown li:last-child{border:0;color:#8a6a10}

/* products */
.section-title{width:1200px;text-align:center;font-weight:600}
.prod-label{width:220px;text-align:center;font-size:11px;font-weight:700;top:320px}
.photo{display:block}
.more-btn{height:38px;width:126px;border-radius:19px;background:var(--orange);color:var(--white);font-weight:700;font-size:16px;line-height:38px;text-align:center;top:529px}

/* features */
.feature-band{left:0;top:627px}
.feature{width:200px;text-align:center}
.feature h3{font-size:20px;font-weight:500;margin:8px 0 22px}
.feature p{font-size:16px;line-height:20px}
.pill{border-radius:34px;background:var(--orange);text-align:center;color:#2a1e00;font-weight:600}

/* certificates */
.cert-shape{border-radius:4px}
.zert{left:0;width:1200px;text-align:center;font-style:italic;font-weight:500;font-size:27px;top:1129px}
.divider{left:0;top:1287px;width:1200px;height:2px;background:var(--yellow)}

/* detail */
.maker{left:140px;top:1314px;width:120px;text-align:center;font-weight:700;font-size:19px}
.yellow-btn{background:var(--yellow);border-radius:18px;font-weight:700;text-align:center}
.stat-label{left:655px;font-size:19px;font-weight:600}
.bar{left:654px;width:409px;height:11px;border-radius:6px;background:var(--grey-bar);overflow:hidden}
.bar span{display:block;height:100%;background:var(--yellow);border-radius:6px}

/* tabs & description */
.tab{top:2174px;font-size:24px}
.tab-line{left:239px;top:2211px;width:171px;height:4px;background:var(--yellow)}
.desc-box{left:50px;top:2259px;width:1098px;height:387px;border-radius:20px;background:var(--yellow)}
.desc-key{left:91px;font-size:24px}
.desc-val{left:446px;font-size:20px}
.desc-bullet{left:435px;font-size:20px}

/* similar */
.card{width:213px;height:320px;top:2850px}
.card-photo{width:213px;height:212px}
.card-foot{width:213px;height:108px;background:var(--yellow);position:relative}
.card-foot h4{position:absolute;left:10px;top:18px;font-size:20px;font-weight:500}
.buy{position:absolute;left:9px;top:68px;width:91px;height:29px;background:#141414;color:var(--white);font-weight:700;font-size:17px;line-height:29px;text-align:center}
.heart{position:absolute;right:10px;top:74px}

/* footer */
.site-footer{left:0;top:3321px;width:1200px;height:330px;background:var(--footer)}
.footer-brand{left:100px;top:3420px;width:175px;text-align:center;color:var(--orange);font-weight:700;font-size:24px;line-height:1.05}
.vline{width:2px;height:138px;background:#e8e8e8;top:3387px}
.vline::before,.vline::after{content:"";position:absolute;left:-3px;width:8px;height:8px;border-radius:50%;background:#e8e8e8}
.vline::before{top:-4px}.vline::after{bottom:-4px}
.newsletter-title{left:395px;top:3392px;color:var(--white);font-size:19px;font-weight:600}
.newsletter-title b{font-size:26px;font-weight:700}
.field{background:#e3e3e3;font-size:9px;padding:5px 8px;color:#333}
.send{left:678px;top:3478px;width:127px;height:22px;background:var(--yellow);font-weight:800;font-size:11px;line-height:22px;text-align:center}
.contact{left:877px;color:var(--white);font-size:11px;display:flex;align-items:center;gap:8px}
.contact-per{left:456px;top:3547px;font-size:20px;font-weight:600;color:var(--orange)}
.contact-per span{color:var(--white)}
.chat-dot{left:716px;top:3535px;width:51px;height:51px;border-radius:50%;background:var(--leaf)}
.social{top:3613px;left:555px;display:flex;gap:6px}
.social span{width:19px;height:19px;border-radius:4px;background:var(--white)}
.copyright{left:0;top:3651px;width:1200px;height:53px;background:var(--yellow);text-align:center;font-size:11px;font-weight:500;line-height:56px}
</style>
</head>
<body>

<header>
  <div class="abs site-header"></div>
  <div class="abs header-accent"></div>
  <div class="abs header-gap"></div>
  <div class="abs header-rule"></div>
  <div class="abs brand"><span class="brand-dot"></span>Auental<br>Landhandel</div>
  <nav class="abs main-nav">
    <span class="active">LANDWIRT</span><span>GESCHÄFTSPARTNER</span><span>LIEFERANTEN</span><span>PRODUKTE ⌄</span><span>FIRMENPRÄSENTATION</span>
  </nav>
  <svg class="abs search-icon" width="26" height="26" viewBox="0 0 26 26" aria-label="Suche"><circle cx="10" cy="10" r="7" fill="none" stroke="#fff" stroke-width="2.2"/><line x1="15" y1="15" x2="23" y2="23" stroke="#fff" stroke-width="2.6" stroke-linecap="round"/></svg>
  <ul class="abs dropdown">
    <li>SOJAEXKTRAKTIONSSCHROT</li><li>MISCHFUTTERMITTEL</li><li>AGRARFOLIEN</li><li>SAATGUT</li>
  </ul>
</header>

<main>
  <h1 class="abs section-title" style="top:219px;font-size:29px">Produkte</h1>

  <div class="abs prod-label" style="left:176px">SOJAEXKTRAKTIONSSCHROT</div>
  <div class="abs prod-label" style="left:381px">MISCHFUTTERMITTEL</div>
  <div class="abs prod-label" style="left:593px">AGRARFOLIEN</div>
  <div class="abs prod-label" style="left:801px">SAATGUT</div>

  <div class="abs photo" role="img" aria-label="Sojabohnen im Jutesack" style="left:178px;top:355px;width:188px;height:188px;background:linear-gradient(135deg,#e6c27a,#c98d34 60%,#8a5a22)"></div>
  <div class="abs photo" role="img" aria-label="Futtermittel aus einem Metalleimer" style="left:387px;top:355px;width:188px;height:188px;background:linear-gradient(160deg,#9a8d7c,#6e5a44 55%,#4a3a2a)"></div>
  <div class="abs photo" role="img" aria-label="Feld mit Strohballen unter Folie" style="left:595px;top:355px;width:188px;height:188px;background:linear-gradient(180deg,#dfe4e8 0%,#c9cfc8 30%,#c08a4a 45%,#9a5e2a 100%)"></div>
  <div class="abs photo" role="img" aria-label="Haufen Saatgutkörner" style="left:822px;top:360px;width:154px;height:160px;border-radius:50%;background:radial-gradient(circle,#c4924f 0%,#b07c3c 55%,rgba(190,140,80,0) 72%)"></div>

  <div class="abs more-btn" style="left:209px">mehr sehen</div>
  <div class="abs more-btn" style="left:418px">mehr sehen</div>
  <div class="abs more-btn" style="left:635px">mehr sehen</div>
  <div class="abs more-btn" style="left:840px">mehr sehen</div>

  <svg class="abs feature-band" width="1200" height="466" viewBox="0 0 1200 466"><polygon points="0,0 1200,0 1200,465 0,307" fill="var(--yellow)"/></svg>

  <div class="abs feature" style="left:172px;top:650px">
    <svg width="44" height="46" viewBox="0 0 44 46"><path d="M22 2 L40 8 V22 C40 34 31 41 22 44 C13 41 4 34 4 22 V8 Z" fill="#111"/><path d="M15 24 L20 29 L30 17" stroke="var(--yellow)" stroke-width="3.5" fill="none"/></svg>
    <h3>Lorem Ipsum</h3>
    <p>Excepteur sint occaecat cupidatat non proident, sunt in Excepteur sint occaecat cupidatat non Excepteur sint occaecat cupidatat non proident, sunt in culpa , sunt in culpa</p>
  </div>
  <div class="abs feature" style="left:390px;top:648px">
    <svg width="44" height="50" viewBox="0 0 44 50"><path d="M12 26 L6 48 L14 43 L18 49 L22 30 Z M32 26 L38 48 L30 43 L26 49 L22 30 Z" fill="#111"/><circle cx="22" cy="18" r="16" fill="#111"/><path d="M15 18 L20 23 L29 13" stroke="var(--yellow)" stroke-width="3.5" fill="none"/></svg>
    <h3>Lorem Ipsum</h3>
    <p>Excepteur sint occaecat cupidatat non proident, sunt in Excepteur sint occaecat cupidatat non Excepteur sint occaecat cupidatat non proident, sunt in culpa , sunt in culpa</p>
  </div>
  <div class="abs feature" style="left:610px;top:652px">
    <svg width="42" height="42" viewBox="0 0 42 42"><circle cx="21" cy="21" r="20" fill="#111"/><path d="M12 22 L18 28 L30 14" stroke="var(--yellow)" stroke-width="4" fill="none"/></svg>
    <h3>Lorem Ipsum</h3>
    <p>Excepteur sint occaecat cupidatat non proident, sunt in Excepteur sint occaecat cupidatat non Excepteur sint occaecat cupidatat non proident, sunt in culpa , sunt in culpa</p>
  </div>
  <div class="abs feature" style="left:827px;top:648px">
    <svg width="50" height="50" viewBox="0 0 50 50"><circle cx="25" cy="14" r="11" fill="none" stroke="#111" stroke-width="3"/><path d="M20 14 L24 18 L31 10" stroke="#111" stroke-width="3" fill="none"/><path d="M3 30 L15 26 L25 33 L35 26 L47 30 L44 42 L35 46 L25 40 L15 46 L6 42 Z" fill="#111"/></svg>
    <h3>Lorem Ipsum</h3>
    <p>Excepteur sint occaecat cupidatat non proident, sunt in Excepteur sint occaecat cupidatat non Excepteur sint occaecat cupidatat non proident, sunt in culpa , sunt in culpa</p>
  </div>

  <div class="abs pill" style="left:852px;top:949px;width:198px;height:67px;line-height:67px;font-size:21px">mehr lesen</div>

  <div class="abs cert-shape" style="left:480px;top:1043px;width:86px;height:86px;background:var(--leaf);border:3px solid #d8d8d8"></div>
  <div class="abs" style="left:585px;top:1068px;font-size:21px;font-weight:500">und</div>
  <div class="abs cert-shape" style="left:640px;top:1046px;width:70px;height:79px;background:#ffffff;border:2px solid #2f7fc4"></div>
  <div class="abs zert">zertifiziert</div>
  <div class="abs pill" style="left:480px;top:1194px;width:240px;height:66px;padding-top:10px;font-size:19px;line-height:23px">herunterladen<br>zertifikat</div>

  <div class="abs divider"></div>

  <div class="abs maker">KORNWERK</div>
  <div class="abs yellow-btn" style="left:300px;top:1344px;width:236px;height:66px;line-height:66px;font-size:23px">Gehe Zur Website</div>

  <div class="abs" style="left:650px;top:1363px;font-size:22px;font-weight:700;color:var(--orange)">Produkt Von <span style="color:var(--ink);font-size:12px">KORNWERK</span></div>
  <div class="abs" style="left:654px;top:1417px;font-size:27px;font-weight:700">Saatgut</div>

  <div class="abs stat-label" style="top:1473px">Feuchtigkeitsgehalt - 10,6%</div>
  <div class="abs bar" style="top:1501px"><span style="width:27%"></span></div>
  <div class="abs stat-label" style="top:1526px">Rohprotein - 32,8%</div>
  <div class="abs bar" style="top:1554px"><span style="width:55%"></span></div>
  <div class="abs stat-label" style="top:1581px">Rohfett - 3,3%</div>
  <div class="abs bar" style="top:1606px"><span style="width:11%"></span></div>
  <div class="abs stat-label" style="top:1635px">Rohfaser - 12,2%</div>
  <div class="abs bar" style="top:1659px"><span style="width:27%"></span></div>
  <div class="abs stat-label" style="top:1690px">Stärke - 5,0%</div>
  <div class="abs bar" style="top:1714px"><span style="width:27%"></span></div>
  <div class="abs stat-label" style="top:1743px">Zucker - 10,5%</div>
  <div class="abs bar" style="top:1770px"><span style="width:27%"></span></div>

  <div class="abs" style="left:655px;top:1823px;font-size:23px;font-weight:700">Besonderheiten</div>
  <div class="abs stat-label" style="top:1864px">Pansenstabilität (Eiweiß) - 75,0%</div>
  <div class="abs bar" style="top:1893px"><span style="width:83%"></span></div>

  <div class="abs" role="img" aria-label="Saatgutkörner als Haufen, Produktfoto" style="left:195px;top:1470px;width:330px;height:315px;border-radius:50%;background:radial-gradient(circle,#d3a466 0%,#c08d4d 50%,rgba(200,150,90,0) 70%)"></div>
  <svg class="abs" style="left:520px;top:1455px" width="36" height="36" viewBox="0 0 36 36" aria-label="Vergrößern"><circle cx="13" cy="13" r="9" fill="none" stroke="#111" stroke-width="3"/><line x1="20" y1="20" x2="32" y2="32" stroke="#111" stroke-width="5" stroke-linecap="round"/></svg>
  <div class="abs" role="img" aria-label="Vorschaubild Saatgut" style="left:168px;top:1806px;width:116px;height:104px;border-radius:50%;background:radial-gradient(circle,#b98548 0%,#a57236 50%,rgba(180,130,70,0) 72%)"></div>

  <svg class="abs" style="left:32px;top:1607px" width="60" height="46" viewBox="0 0 60 46" aria-label="Zurück"><polygon points="0,23 60,0 60,46" fill="var(--orange)"/></svg>
  <svg class="abs" style="left:1120px;top:1607px" width="60" height="46" viewBox="0 0 60 46" aria-label="Weiter"><polygon points="60,23 0,0 0,46" fill="var(--orange)"/></svg>

  <div class="abs yellow-btn" style="left:381px;top:2011px;width:451px;height:67px;line-height:67px;font-size:24px;border-radius:20px;text-decoration:underline">Weitere Informationen Anfordern</div>

  <div class="abs tab" style="left:248px">Beschreibung</div>
  <div class="abs tab-line"></div>
  <div class="abs tab" style="left:461px">Zusatzliche Informationen</div>
  <div class="abs tab" style="left:806px">Ein Muster Anfragen</div>

  <div class="abs desc-box"></div>
  <div class="abs desc-key" style="top:2288px">Zusammensetzung</div>
  <div class="abs desc-key" style="top:2332px">Einsatzempfehlung</div>
  <div class="abs desc-key" style="top:2376px">Haltbarkeit</div>
  <div class="abs desc-key" style="top:2420px">Vorteile</div>
  <div class="abs desc-val" style="top:2292px">Rapsschrot</div>
  <div class="abs desc-val" style="top:2336px">Milchkühe: Bis Zu 3 Kg Pro Tier Pro Tag, Abhängig Von Der Ration</div>
  <div class="abs desc-val" style="top:2380px;left:449px">Mehrere Monate Bei Trockener Lagerung</div>
  <div class="abs desc-bullet" style="top:2425px">• Das Futterprotein Wird Effizient Genutzt</div>
  <div class="abs desc-bullet" style="top:2462px">• Gute Futteraufnahme Durch Gute Schmackhaftigkeit</div>
  <div class="abs desc-bullet" style="top:2499px">• Hoher Pansenschutz Der Proteine</div>
  <div class="abs desc-bullet" style="top:2537px">• Hohe Dünndarmverdaulichkeit</div>
  <div class="abs desc-bullet" style="top:2574px">• Geringere Umweltbelastung Durch Reduzierte Stickstoffausscheidung</div>

  <h2 class="abs" style="left:68px;top:2736px;font-size:31px;font-weight:700">Ähnliche Produkte</h2>

  <article class="abs card" style="left:50px">
    <div class="card-photo" role="img" aria-label="Saatgutkörner als Haufen" style="background:radial-gradient(circle at 50% 55%,#c4924f 0%,#b07c3c 45%,rgba(190,140,80,0) 66%)"></div>
    <div class="card-foot"><h4>Lorem Ipsum</h4><div class="buy">Kaufen</div><svg class="heart" width="22" height="20" viewBox="0 0 22 20"><path d="M11 19 C4 13 1 10 1 6 A5 5 0 0 1 11 4 A5 5 0 0 1 21 6 C21 10 18 13 11 19Z" fill="var(--heart)"/></svg></div>
  </article>
  <article class="abs card" style="left:345px">
    <div class="card-photo" role="img" aria-label="Futtermittel aus einem Metalleimer" style="background:linear-gradient(160deg,#9a8d7c,#6e5a44 55%,#4a3a2a)"></div>
    <div class="card-foot"><h4>Lorem Ipsum</h4><div class="buy">Kaufen</div><svg class="heart" width="22" height="20" viewBox="0 0 22 20"><path d="M11 19 C4 13 1 10 1 6 A5 5 0 0 1 11 4 A5 5 0 0 1 21 6 C21 10 18 13 11 19Z" fill="var(--heart)"/></svg></div>
  </article>
  <article class="abs card" style="left:640px">
    <div class="card-photo" role="img" aria-label="Sojabohnen im Jutesack" style="background:linear-gradient(135deg,#e6c27a,#c98d34 60%,#8a5a22)"></div>
    <div class="card-foot"><h4>Lorem Ipsum</h4><div class="buy">Kaufen</div><svg class="heart" width="22" height="20" viewBox="0 0 22 20"><path d="M11 19 C4 13 1 10 1 6 A5 5 0 0 1 11 4 A5 5 0 0 1 21 6 C21 10 18 13 11 19Z" fill="var(--heart)"/></svg></div>
  </article>
  <article class="abs card" style="left:935px">
    <div class="card-photo" role="img" aria-label="Feld mit Strohballen unter Folie" style="background:linear-gradient(180deg,#dfe4e8 0%,#c9cfc8 30%,#c08a4a 45%,#9a5e2a 100%)"></div>
    <div class="card-foot"><h4>Lorem Ipsum</h4><div class="buy">Kaufen</div><svg class="heart" width="22" height="20" viewBox="0 0 22 20"><path d="M11 19 C4 13 1 10 1 6 A5 5 0 0 1 11 4 A5 5 0 0 1 21 6 C21 10 18 13 11 19Z" fill="var(--heart)"/></svg></div>
  </article>
</main>

<footer>
  <div class="abs site-footer"></div>
  <div class="abs footer-brand"><span class="brand-dot" style="width:34px;height:34px;margin-bottom:10px"></span>Auental<br>Landhandel</div>
  <div class="abs vline" style="left:356px"></div>
  <div class="abs vline" style="left:842px"></div>
  <div class="abs newsletter-title">Abonnieren Sie Unseren <b>Newsletter</b></div>
  <div class="abs field" style="left:395px;top:3428px;width:127px;height:21px">Name</div>
  <div class="abs field" style="left:536px;top:3428px;width:126px;height:21px">Email</div>
  <div class="abs field" style="left:678px;top:3428px;width:127px;height:21px">Telefonnummer</div>
  <div class="abs field" style="left:395px;top:3468px;width:267px;height:33px;padding-top:10px">Nachricht</div>
  <div class="abs send">SCHICKEN</div>

  <div class="abs contact" style="top:3437px"><svg width="10" height="12" viewBox="0 0 10 12"><path d="M5 12 C2 8 0 6 0 4 A5 5 0 0 1 10 4 C10 6 8 8 5 12Z" fill="#fff"/><circle cx="5" cy="4" r="1.8" fill="#262626"/></svg>Locatins</div>
  <div class="abs contact" style="top:3456px"><svg width="10" height="10" viewBox="0 0 10 10"><circle cx="5" cy="5" r="5" fill="#fff"/><path d="M3 2.5 L4.2 4.5 L3.6 5 C4 6 4.8 6.6 5.4 6.8 L6 6 L7.8 7.2 L7 8.3 C4.5 8 2.2 5.6 2 3.2Z" fill="#262626"/></svg>+49 761 000 1234</div>
  <div class="abs contact" style="top:3475px"><svg width="10" height="8" viewBox="0 0 10 8"><rect width="10" height="8" fill="#fff"/><path d="M0 0 L5 4.5 L10 0" stroke="#262626" fill="none"/></svg>info@auental-landhandel.de</div>

  <div class="abs contact-per">Kontaktieren Sie Uns <span>per</span></div>
  <div class="abs chat-dot" aria-label="Chat"></div>
  <div class="abs social"><span></span><span></span><span></span><span></span></div>
  <div class="abs copyright">Copyright 2023 All Right Reserved</div>
</footer>

</body>
</html>
```